Professional Package for CPA Firm

We would like a stationery design for our new CPA Firm based in Atlanta, GA called 'Vale 8'. We work with investors to help grow investments, tax free. We would like the design to have a professional/minimal look with a 'wow' factor. We need 9.5″ x 4.125″, 9x12, and 10x13 mailing envelopes, business cards, and a letterhead. We have a logo that is already complete. For the letterhead, we would like to have space to put credentials at the bottom of the page

Industry/Entity Type

CPA, Accounting

```html
<!DOCTYPE html>
<html lang="en">
<head>
<meta charset="utf-8">
<title>Vale 8 — Business Card</title>
<link rel="stylesheet" href="https://fonts.googleapis.com/css2?family=Montserrat:wght@600;700&family=Roboto:wght@400;500&display=swap">
<style>
  :root {
    --stage: #3b3b3d;
    --paper: #ffffff;
    --ink: #111111;
    --text-grey: #4a4a4a;
    --rule: #222222;
    --brand-blue: #1e9ad6;
    --brand-blue-light: #3bb3ea;
    --brand-blue-deep: #1283bd;
  }
  * { box-sizing: border-box; margin: 0; padding: 0; }
  html, body {
    width: 1200px; height: 900px; overflow: hidden;
    background: var(--stage);
  }
  .stage {
    width: 1200px; height: 900px;
    display: flex; flex-direction: column;
    align-items: center; justify-content: center; gap: 40px;
  }
  .card {
    width: 700px; height: 400px;
    position: relative;
    box-shadow: 0 14px 30px rgba(0,0,0,0.35);
  }

  /* Front */
  .card-front {
    background: var(--paper);
    display: flex; align-items: center;
  }
  .brand-block {
    width: 330px;
    display: flex; flex-direction: column; align-items: center;
  }
  .brand-name {
    display: flex; align-items: center; gap: 14px;
    font-family: "Montserrat", sans-serif; font-weight: 700;
    font-size: 54px; letter-spacing: 1px; color: var(--ink);
    line-height: 1;
  }
  .brand-square {
    width: 34px; height: 34px; background: var(--brand-blue);
  }
  .brand-tagline {
    margin-top: 12px;
    font-family: "Roboto", sans-serif; font-size: 15px;
    letter-spacing: 1.5px; color: var(--ink);
  }
  .divider {
    width: 2px; height: 190px; background: var(--rule);
  }
  .contact-block {
    padding-left: 40px;
    font-family: "Roboto", sans-serif;
  }
  .person-name {
    font-family: "Montserrat", sans-serif; font-weight: 700;
    font-size: 24px; color: var(--ink); letter-spacing: 0.5px;
  }
  .person-title {
    font-size: 19px; color: var(--brand-blue); font-weight: 500;
    margin-top: 4px;
  }
  .address {
    margin-top: 16px; font-size: 17px; line-height: 1.3; color: var(--text-grey);
  }
  .contact-list { list-style: none; margin-top: 4px; }
  .contact-list li {
    display: flex; align-items: center; gap: 10px;
    font-size: 17px; line-height: 1.35; color: var(--text-grey);
  }
  .contact-icon { width: 15px; height: 15px; flex: none; }

  /* Back */
  .card-back {
    background: var(--brand-blue);
    overflow: hidden;
  }
  .pattern-field {
    position: absolute; inset: 0;
    background: linear-gradient(135deg, var(--brand-blue-light) 0%, var(--brand-blue) 55%, var(--brand-blue-deep) 100%);
  }
  .back-mark {
    position: absolute; left: 50%; top: 50%;
    transform: translate(-50%, -50%);
    font-family: "Montserrat", sans-serif; font-weight: 700;
    font-size: 40px; color: var(--paper); letter-spacing: 1px;
  }
</style>
</head>
<body>
<main class="stage">
  <section class="card card-front" aria-label="Business card front">
    <div class="brand-block">
      <div class="brand-name"><span class="brand-square"></span>Vale 8</div>
      <p class="brand-tagline">CPAs and Tax Advisors</p>
    </div>
    <div class="divider"></div>
    <div class="contact-block">
      <h1 class="person-name">MARTIN ELLSWORTH</h1>
      <p class="person-title">Managing Director</p>
      <p class="address">48 Harlow Creek Road,<br>Marston, GA 30318</p>
      <ul class="contact-list">
        <li>
          <svg class="contact-icon" viewBox="0 0 16 16" aria-hidden="true"><path d="M3 1.5l2.5 0 1.2 3.2-1.6 1.1c.8 1.8 2.3 3.3 4.1 4.1l1.1-1.6 3.2 1.2 0 2.5c0 .8-.7 1.5-1.5 1.5C6.5 13.5 2.5 9.5 1.5 3c0-.8.7-1.5 1.5-1.5z" fill="var(--brand-blue)"/></svg>
          +1 404 555 0187
        </li>
        <li>
          <svg class="contact-icon" viewBox="0 0 16 16" aria-hidden="true"><rect x="1" y="3" width="14" height="10" rx="1" fill="var(--brand-blue)"/><path d="M1.5 3.5L8 9l6.5-5.5" stroke="#fff" stroke-width="1.3" fill="none"/></svg>
          info@valeeight.com
        </li>
        <li>
          <svg class="contact-icon" viewBox="0 0 16 16" aria-hidden="true"><g fill="none" stroke="var(--brand-blue)" stroke-width="1.4"><circle cx="8" cy="8" r="6.5"/><ellipse cx="8" cy="8" rx="3" ry="6.5"/><path d="M1.5 8h13M2.5 4.8h11M2.5 11.2h11"/></g></svg>
          www.valeeight.com
        </li>
      </ul>
    </div>
  </section>

  <section class="card card-back" aria-label="Business card back">
    <div class="pattern-field" role="img" aria-label="Repeating embossed brand pattern in blue across the card back"></div>
    <p class="back-mark">Vale 8</p>
  </section>
</main>
</body>
</html>
```